R.Tomkins LLC Organizational Change and Development

I am starting my own company as a a senior facilitator, keynote speaker, executive coach, webinar training instructor, quality management adviser, and classroom presenter. I have taught diversity and cultural competence, organizational development, change management, leadership, organizational dynamics, team-building, accountability, negotiation, work-life balance, quality management, DISC, and hundreds of web based trainings. I have a PhD. in Counseling Psychology, MBA, B.S. in Human Development, Family Studies, and a Master’s Practitioner of Neurolinguistic Programming. My degrees and certifications give me a foundation for advising a wide variety of people, industries, and cultures at all organizational levels. I would like a design that's fun, engaging, humorous, progressive, and has a professional feel. I really like the colors burgundy wine.

Target Market(s)

corporate America

Industry/Entity Type

Training

Number of Pages Required

5+ page

Colors
eb1f26
f04a50
3176b4
33a6d7

Requirements
Must have
• my different areas of expertise - fun visuals -easy for me to use
Should not have
• something that looks stiff, too traditional or boring

```html
<!DOCTYPE html>
<html lang="en">
<head>
<meta charset="utf-8">
<title>R.Tomkins LLC – Organizational Change and Development</title>
<link rel="stylesheet" href="https://fonts.googleapis.com/css2?family=Mulish:wght@400;600;700&display=swap">
<style>
:root{
  --sky:#33a6d7;
  --ocean:#3176b4;
  --red:#eb1f26;
  --red-soft:#f04a50;
  --red-deep:#c9161c;
  --ink:#333;
  --white:#fff;
}
*{box-sizing:border-box;margin:0;padding:0}
html,body{width:784px;height:1200px;overflow:hidden}
body{
  font-family:"Mulish",sans-serif;color:var(--ink);position:relative;
  background:linear-gradient(to bottom,var(--sky) 0,var(--sky) 1070px,var(--ocean) 1070px);
}
.abs{position:absolute}

/* top bar */
.topbar{top:15px;left:515px;display:flex;align-items:center;color:var(--white);font-size:12px}
.topbar svg{margin-right:5px}
.topbar .divider{width:1px;height:16px;background:rgba(255,255,255,.8);margin:0 10px}
.social{display:flex;gap:4px}
.social span{width:16px;height:16px;border:1.3px solid var(--white);border-radius:50%}

/* hero */
.hero{top:39px;left:66px;width:653px;height:248px;display:flex}
.brand{width:212px;height:100%;background:radial-gradient(circle at 50% 45%,#fafafa 0,#e8e8e8 55%,#d2d2d2 100%);
  display:flex;align-items:center;justify-content:center}
.brand-name{font-size:22px;font-weight:600;color:var(--ink);line-height:1;white-space:nowrap}
.slide{flex:1;background:#000;position:relative;overflow:hidden}
.slide-photo{position:absolute;right:0;top:0;width:190px;height:100%;
  background:radial-gradient(ellipse at 60% 40%,#5a3a2a 0,#2b1c16 45%,#000 85%)}
.slide-title{position:absolute;left:15px;top:114px;color:var(--red);font-size:16px;font-weight:700}
.slide-sub{position:absolute;left:15px;top:136px;color:var(--white);font-size:8.8px}
.slide-arrows{position:absolute;left:11px;top:220px;display:flex;gap:5px}
.slide-arrows svg{display:block}

/* nav */
.nav{top:287px;left:66px;width:653px;height:51px;
  background:linear-gradient(to bottom,var(--red-soft),var(--red) 45%,var(--red-deep))}
.nav-link{position:absolute;color:var(--white);font-size:12.2px;font-weight:600;top:18px}
.search{position:absolute;left:444px;top:16px;width:192px;height:21px;border:1px solid #f7a0a3;
  background:var(--red-deep);color:#f3c9ca;font-size:8.5px;padding:4px 5px;box-shadow:inset 0 1px 3px rgba(0,0,0,.3)}

/* content */
.page{top:338px;left:66px;width:653px;height:789px;background:var(--white)}
.nav-shadow{top:338px;left:66px;width:653px;height:18px;
  background:radial-gradient(ellipse at 50% 0,rgba(0,0,0,.35) 0,rgba(0,0,0,0) 70%)}
.section-title{left:66px;width:653px;text-align:center;color:var(--red);font-size:19px;font-weight:600}
.welcome-text{left:353px;top:397px;width:356px;font-size:8.7px;line-height:14.1px;color:#333}
.welcome-text p+p{margin-top:14px}

.card{width:194px}
.card-photo{width:194px;height:102px}
.card-title{color:var(--red);font-size:11.4px;font-weight:600;margin-top:12px}
.card-text{font-size:8.6px;line-height:14px;margin-top:7px;color:#333}
.read-more{display:inline-block;background:var(--red);color:var(--white);font-size:7.2px;font-weight:600;
  padding:2px 6px;border-radius:1px;box-shadow:1px 1px 0 rgba(0,0,0,.15)}

/* footer */
.footer{color:var(--white);font-size:8.8px;line-height:15px}
</style>
</head>
<body>

<div class="abs topbar">
  <svg width="16" height="16" viewBox="0 0 16 16" aria-hidden="true">
    <circle cx="8" cy="8" r="7.2" fill="none" stroke="#fff" stroke-width="1.3"/>
    <path d="M5.3 4.2l1.3-.3.9 2-.8.7c.4.9 1.1 1.6 2 2l.7-.8 2 .9-.3 1.3c-3 .3-6.1-2.8-5.8-5.8z" fill="#fff"/>
  </svg>
  <span>(555) 014-2290</span>
  <span class="divider"></span>
  <div class="social" aria-label="Social links"><span></span><span></span><span></span><span></span></div>
</div>

<header class="abs hero">
  <div class="brand">
    <div class="brand-name">R.Tomkins LLC</div>
  </div>
  <div class="slide">
    <div class="slide-photo" role="img" aria-label="Portrait of the consultant in a dark blazer"></div>
    <div class="slide-title">PhD. in Counseling Psychology</div>
    <div class="slide-sub">MBA in Human Development &amp; Family Studies</div>
    <div class="slide-arrows">
      <svg width="14" height="14" viewBox="0 0 14 14"><circle cx="7" cy="7" r="7" fill="#3176b4"/><path d="M8.2 4L5.2 7l3 3" stroke="#fff" stroke-width="1.6" fill="none"/></svg>
      <svg width="14" height="14" viewBox="0 0 14 14"><circle cx="7" cy="7" r="7" fill="#3176b4"/><path d="M5.8 4l3 3-3 3" stroke="#fff" stroke-width="1.6" fill="none"/></svg>
    </div>
  </div>
</header>

<nav class="abs nav">
  <span class="nav-link" style="left:24px">Home</span>
  <span class="nav-link" style="left:91px">About&nbsp; Us</span>
  <span class="nav-link" style="left:177px">Services</span>
  <span class="nav-link" style="left:255px">FAQ's</span>
  <span class="nav-link" style="left:319px">Contact Us</span>
  <div class="search">Search</div>
</nav>

<main class="abs page"></main>
<div class="abs nav-shadow"></div>

<h1 class="abs section-title" style="top:354px">WELCOME TO R.TOMKINS</h1>
<div class="abs" style="left:71px;top:400px;width:272px;height:147px;background:linear-gradient(160deg,#6fb2e6 0,#a9d3f2 45%,#c89a80 75%,#3c9fb4 100%)" role="img" aria-label="Smiling family of five against a blue sky"></div>
<div class="abs welcome-text">
  <p>Lorem Ipsum is simply dummy text of the printing and typesetting industry. Lorem Ipsum has been the industry's standard dummy text ever since the 1500s, when an unknown printer took a galley of type and scrambled it to make a type specimen book. It has survived not only five centuries, but also the leap into electronic typesetting, remaining essentially unchanged. It was popularised in the 1960s with the release of Letraset sheets containing Lorem Ipsum passages, and more recently with desktop publishing software like Aldus PageMaker including versions of Lorem Ipsum.</p>
  <p>Lorem Ipsum is simply dummy text of the printing and typesetting industry. Lorem Ipsum has been the industry's standard dummy text ever since the 1500s, when an unknown printer took a galley of type and scrambled</p>
</div>

<h2 class="abs section-title" style="top:586px">OUR SERVICES</h2>

<article class="abs card" style="left:71px;top:640px">
  <div class="card-photo" style="background:linear-gradient(135deg,#b52a2a,#d44a3c 50%,#3a2622)" role="img" aria-label="Group of women meeting around a table"></div>
  <h3 class="card-title">Senior Facilitator</h3>
  <p class="card-text">Lorem Ipsum is simply dummy text of the printing and typesetting industry. Lorem Ipsum has been the industry's standard dummy text ever since the 1500s</p>
  <span class="read-more" style="margin-top:6px">Read More</span>
</article>
<article class="abs card" style="left:294px;top:640px">
  <div class="card-photo" style="background:linear-gradient(90deg,#fafafa,#e6e6e6 60%,#3a3a3a);border:1px solid #ddd" role="img" aria-label="Woman speaking into a microphone"></div>
  <h3 class="card-title">Keynote Speaker</h3>
  <p class="card-text">Lorem Ipsum is simply dummy text of the printing and typesetting industry. Lorem Ipsum has been the industry's standard dummy text ever since the 1500s</p>
  <span class="read-more" style="margin-top:6px">Read More</span>
</article>
<article class="abs card" style="left:518px;top:640px">
  <div class="card-photo" style="background:linear-gradient(135deg,#6d7a5a,#d8d4cc 45%,#2f3440)" role="img" aria-label="Presenter coaching a business team"></div>
  <h3 class="card-title">Executive Coach</h3>
  <p class="card-text">Lorem Ipsum is simply dummy text of the printing and typesetting industry. Lorem Ipsum has been the industry's standard dummy text ever since the 1500s</p>
  <span class="read-more" style="margin-top:6px">Read More</span>
</article>

<article class="abs card" style="left:71px;top:866px">
  <div class="card-photo" style="background:linear-gradient(135deg,#c9a886,#e8e2d8 50%,#7b7f88)" role="img" aria-label="Students learning on laptops"></div>
  <h3 class="card-title" style="margin-top:10px">Webinar Training Instructor</h3>
  <p class="card-text">Lorem Ipsum is simply dummy text of the printing and typesetting industry. Lorem Ipsum has been the industry's standard dummy text ever since the 1500s</p>
  <span class="read-more" style="margin-top:22px">Read More</span>
</article>
<article class="abs card" style="left:294px;top:866px">
  <div class="card-photo" style="background:radial-gradient(circle at 50% 75%,#9aa4b8 0,#3a4160 50%,#1c2036 100%)" role="img" aria-label="Compass pointing to the word quality"></div>
  <h3 class="card-title" style="margin-top:10px">Quality Management Adviser</h3>
  <p class="card-text">Lorem Ipsum is simply dummy text of the printing and typesetting industry. Lorem Ipsum has been the industry's standard dummy text ever since the 1500s</p>
  <span class="read-more" style="margin-top:22px">Read More</span>
</article>
<article class="abs card" style="left:518px;top:866px">
  <div class="card-photo" style="background:linear-gradient(180deg,#e4e4e2,#b8aca0 50%,#5a463a)" role="img" aria-label="Audience in a lecture classroom"></div>
  <h3 class="card-title" style="margin-top:12px">Classroom Presenter</h3>
  <p class="card-text">Lorem Ipsum is simply dummy text of the printing and typesetting industry. Lorem Ipsum has been the industry's standard dummy text ever since the 1500s</p>
  <span class="read-more" style="margin-top:20px">Read More</span>
</article>

<footer>
  <div class="abs footer" style="left:66px;top:1147px">
    <div>© 2014 Company Name,All Rights Reserved</div>
    <div style="margin-top:4px">Terms &amp; Conditions | Privacy Policy | Legal Notice</div>
  </div>
  <address class="abs footer" style="right:63px;top:1154px;text-align:right;font-style:normal">
    2210 North Alder Grove Lane,<br>Suite 100, Riverton City, Utah 84000
  </address>
</footer>

</body>
</html>
```